Create a wordpress website for Tovarin business solution

This project is to create a complete website with all pages.

Overview
The purpose of this project is to create a full complete website with all pages (16 pages). The site should be professional and modern. The site is for an IT recruiting and IT training company. The site needs to be easy to administer and update content. It should be simple to add pages, videos and testimonials later. I will leave the site layout, color schemes and flow to the designers.

Navigation Menu (Home, who we are, what we do, what makes us different, why it matters, candidate portal, contact us, Blog)

WHO WE ARE should be a drop down menu with link to pages (about us, mission, vision and purpose, our team)

WHAT WE DO should be drop down menu with link to the following pages (IT Recruiting, IT Training, Hardware and software sales)

What makes us different should be single page with different paragraph titles. (We live what we do, we don't compromise quality, we share knowledge, staffing guarantee)

Why it matters should be single page with paragraph titles. (Quickly fill positions, candidate career development)

Candidate portal should links to my portal login page. I can add the correct URL later. I just need it to link to somewhere. I can change it.

Contact us should have (address, phone number, google map and a form to submit request for a call back)

Blog - This link should launch a wordpress blogging module

Target Market(s)

IT RECRUITING AND CONSULTING

Industry/Entity Type

It Company

Coding

Coded - Design and coding required

Requirements
Must have
• Company Logo
• Navigation Menu (Home, who we are, what we do, what makes us different, why it matters, candidate portal, contact us)
• WHO WE ARE should be a drop down menu with link to pages (about us, mission, vision and purpose, our team)
• WHAT WE DO should be drop down menu with link to the following pages (IT Recruiting, IT Training, Hardware and software sales)
• What makes us different should be single page with different paragraph titles. (We live what we do, we don't compromise quality, we share knowledge, staffing guarantee)
• Why it matters should be single page with paragraph titles. (Quickly fill positions, candidate career development)
• Candidate portal should links to my portal login page. I can add the correct URL later. I just need it to link to somewhere. I can change it.
• Contact us should have (address, phone number, google map and a form to submit request for a call back)

```html
<!DOCTYPE html>
<html lang="en">
<head>
<meta charset="utf-8">
<title>Tovarin Business Solution</title>
<link href="https://fonts.googleapis.com/css2?family=Open+Sans:wght@400;600;700&family=Roboto+Condensed:wght@400;700&family=Roboto:wght@400;500;700&display=swap" rel="stylesheet">
<style>
:root{
  --orange:#f58a1f;
  --orange-dark:#e07512;
  --blue:#1d63a9;
  --ink:#333;
  --muted:#666;
  --light:#ececec;
  --white:#fff;
}
*{box-sizing:border-box;margin:0;padding:0}
html,body{width:1200px;height:4128px;overflow:hidden}
body{position:relative;background:var(--white);font-family:'Open Sans',sans-serif;color:var(--ink)}
section,header,nav,footer,.topbar{position:absolute;left:0;width:1200px}
.abs{position:absolute}

/* top bar */
.topbar{top:0;height:47px;background:#f4f4f4}
.topbar .social{left:80px;top:14px;display:flex;gap:18px}
.dot{width:18px;height:18px;border-radius:50%;background:#7b8da3}
.topbar .login{right:113px;top:12px;font-size:16px;color:#888;display:flex;align-items:center;gap:6px}

/* header */
header{top:47px;height:77px;background:var(--white)}
.brand{left:77px;top:14px;display:flex;align-items:center;gap:12px}
.brand-mark{width:40px;height:40px;background:var(--blue)}
.brand-name{font-family:'Open Sans',sans-serif;font-weight:700;font-size:38px;line-height:48px;color:var(--blue)}
.call{right:77px;top:14px;display:flex;align-items:center;gap:14px}
.call-label{font-family:'Roboto',sans-serif;color:var(--orange);font-size:24px}
.call-icon{width:46px;height:46px;border:2px solid #333;border-radius:50%;display:flex;align-items:center;justify-content:center}
.call-num{font-family:'Roboto',sans-serif;font-weight:700;color:var(--blue);font-size:27px}

/* nav */
nav{top:124px;height:58px;background:var(--orange)}
.menu{position:absolute;left:77px;top:0;height:58px;display:flex;list-style:none}
.menu li{font-family:'Roboto Condensed',sans-serif;color:var(--white);font-size:17px;line-height:58px;padding:0 12px;text-transform:uppercase;white-space:nowrap}
.menu li.active{background:var(--blue);padding:0 23px}

/* hero */
.hero{top:182px;height:575px;background:linear-gradient(100deg,#c9d3dc 0%,#e6e9ec 35%,#b9b2ac 60%,#6b6f7a 85%,#a4aab3 100%)}
.hero h1{left:77px;top:150px;font-family:'Roboto',sans-serif;font-weight:700;font-size:54px;color:var(--blue)}
.hero p{left:77px;top:235px;font-size:25px;color:#222}
.btn{display:inline-flex;align-items:center;justify-content:center;gap:8px;font-family:'Roboto Condensed',sans-serif;color:var(--white);text-transform:uppercase;border-radius:2px;white-space:nowrap}
.btn-orange{background:var(--orange-dark);font-size:17px}
.btn-blue{background:var(--blue);font-size:18px}
.hero .btn{left:77px;top:300px;width:201px;height:49px}

/* welcome */
.welcome{top:757px;height:349px;background:var(--light)}
.video{left:77px;top:60px;width:385px;height:234px;background:linear-gradient(135deg,#e6e6e6,#aab0b8 60%,#7d838c);border:3px solid #9a9a9a}
.play{left:159px;top:84px;width:60px;height:60px;border-radius:50%;background:rgba(40,40,40,.75)}
.welcome h2{left:517px;top:52px;font-family:'Roboto',sans-serif;font-size:44px;font-weight:400;color:var(--blue);white-space:nowrap}
.accent{color:var(--orange)}
.welcome p{left:517px;top:122px;width:606px;font-size:15px;line-height:24px;color:var(--muted)}
.welcome .btn{left:517px;top:247px;width:168px;height:50px}

/* mission */
.mission{top:1106px;height:242px;background:var(--orange)}
.col{top:40px;width:520px;color:var(--white)}
.col h3{font-family:'Roboto',sans-serif;font-weight:400;font-size:42px;display:flex;align-items:center;gap:14px;white-space:nowrap}
.col p{font-size:14px;line-height:23px;margin-top:8px;padding-left:48px;color:#fff8ee}
.col p u{margin-left:6px}
.divider{left:581px;top:38px;width:2px;height:170px;background:rgba(255,255,255,.7)}

/* section heads */
.sec-title{left:0;width:1200px;text-align:center;font-family:'Roboto',sans-serif;font-size:46px;font-weight:400}
.sec-sub{left:150px;width:900px;text-align:center;font-size:15px;line-height:24px}

/* what we do */
.what{top:1348px;height:570px;background:var(--white)}
.what .sec-title{top:40px;color:var(--blue)}
.what .sec-sub{top:114px;color:var(--muted)}
.photo{background:linear-gradient(135deg,#d9dde2,#8f969f)}
.card{width:325px;text-align:center}
.card .photo{width:325px;height:188px}
.card h4{font-family:'Roboto',sans-serif;font-weight:400;font-size:22px;color:var(--orange);margin-top:18px}
.card p{font-size:14px;line-height:23px;color:var(--muted);margin-top:6px;padding:0 24px}
.more{color:var(--orange);text-transform:uppercase;font-size:13px;margin-left:6px}

/* why it matters */
.why{top:1918px;height:394px;background:linear-gradient(90deg,#1a5a9c,#2b6fb2 50%,#1d609f)}
.why .sec-title{top:45px;color:var(--white)}
.why .sec-sub{left:300px;width:600px;top:116px;color:#e8f0f8}
.point{top:215px;display:flex;gap:27px;color:var(--white)}
.badge{width:126px;height:126px;border-radius:50%;background:var(--white);display:flex;align-items:center;justify-content:center;flex:none}
.point h4{font-family:'Roboto',sans-serif;font-weight:400;font-size:23px;margin-top:22px;white-space:nowrap}
.point p{font-size:14px;line-height:23px;margin-top:6px;color:#e8f0f8}
.point .more{color:var(--white)}

/* different */
.diff{top:2312px;height:528px;background:var(--white)}
.diff .sec-title{top:50px;color:var(--blue)}
.diff .sec-sub{top:122px;color:var(--muted)}
.tile{width:234px;top:214px;text-align:center}
.tile .photo{height:138px}
.tile h4{font-family:'Roboto',sans-serif;font-weight:500;font-size:21px;color:var(--blue);margin-top:26px;line-height:24px}
.tile p{font-size:14px;line-height:23px;color:var(--muted);margin-top:6px}
.tile .more{color:var(--blue)}

/* team */
.team{top:2840px;height:696px;background:linear-gradient(90deg,#e27a14,#f39a3e 50%,#e27a14)}
.team .sec-title{top:45px;color:var(--white)}
.team .sec-sub{left:230px;width:740px;top:120px;color:#fff3e4}
.member{top:220px;width:209px;color:var(--white)}
.member .photo{height:229px;background:linear-gradient(160deg,#f1f1f1,#b5b7ba 55%,#555a62)}
.member h4{font-family:'Roboto',sans-serif;font-weight:500;font-size:22px;margin-top:28px}
.member .row{display:flex;align-items:flex-start;gap:10px;margin-top:4px;font-size:14px;line-height:22px}
.member .row span{flex:1}
.team .btn{left:504px;top:594px;width:192px;height:50px}

/* contact */
.contact{top:3536px;height:532px;background:#f0f0f0}
.contact h2{left:77px;top:50px;font-family:'Roboto',sans-serif;font-weight:400;font-size:46px;color:var(--blue)}
.contact h5{left:77px;top:136px;font-family:'Roboto',sans-serif;font-weight:700;font-size:20px;color:var(--orange)}
.info{font-size:14px;line-height:23px;color:#555;display:flex;gap:14px}
.map{left:77px;top:275px;width:501px;height:207px;background:linear-gradient(160deg,#eef0f2,#dfe3e7)}
.field{left:622px;width:501px;height:48px;border:1px solid #cfcfcf;background:var(--white);font-size:14px;color:#888;padding:14px 16px}
.field.msg{height:97px}
.contact .btn{left:999px;top:446px;width:124px;height:50px}

footer{top:4068px;height:60px;background:var(--orange)}
footer p{left:77px;top:20px;font-size:13px;color:var(--white)}
footer .social{right:77px;top:13px;display:flex;gap:12px}
footer .dot{width:34px;height:34px;background:var(--blue)}
</style>
</head>
<body>

<div class="topbar">
  <div class="abs social"><span class="dot"></span><span class="dot"></span><span class="dot"></span></div>
  <div class="abs login">
    <svg width="14" height="16" viewBox="0 0 14 16"><rect x="1" y="7" width="12" height="9" rx="1" fill="#999"/><path d="M4 7V4a3 3 0 0 1 6 0v3" stroke="#999" stroke-width="2" fill="none"/></svg>
    Login
  </div>
</div>

<header>
  <div class="abs brand">
    <span class="brand-mark"></span>
    <span class="brand-name">Tovarin</span>
  </div>
  <div class="abs call">
    <span class="call-label">Call us now</span>
    <span class="call-icon"><svg width="22" height="22" viewBox="0 0 24 24"><path d="M6.6 10.8a15 15 0 0 0 6.6 6.6l2.2-2.2a1 1 0 0 1 1-.25 11.4 11.4 0 0 0 3.6.57 1 1 0 0 1 1 1V20a1 1 0 0 1-1 1A17 17 0 0 1 3 4a1 1 0 0 1 1-1h3.5a1 1 0 0 1 1 1c0 1.25.2 2.45.57 3.57a1 1 0 0 1-.25 1z" fill="#333"/></svg></span>
    <span class="call-num">123 456 7890</span>
  </div>
</header>

<nav>
  <ul class="menu">
    <li class="active">Home</li><li>Who we are</li><li>What we do</li><li>What makes us different</li><li>Why it matters</li><li>Candidate portal</li><li>Contact us</li>
  </ul>
</nav>

<section class="hero" role="img" aria-label="Photo of smiling business team seated at a meeting table">
  <h1 class="abs">TOVARIN</h1>
  <p class="abs">Lorem Ipsum is simply dummy</p>
  <span class="abs btn btn-orange">Contact us now</span>
</section>

<section class="welcome">
  <div class="abs video" role="img" aria-label="Video preview of a team meeting">
    <svg class="abs play" viewBox="0 0 60 60"><polygon points="24,18 42,30 24,42" fill="#fff"/></svg>
  </div>
  <h2 class="abs">WELCOME TO <span class="accent">TOVARIN</span></h2>
  <p class="abs">Lorem Ipsum is simply dummy text of the printing and typesetting industry. Lorem Ipsum has been the industry's standard dummy text ever since the 1500s, when an unknown printer took a galley of type and scrambled it to make a type specimen book. It has survived not only five centuries, but also the leap into electronic type...</p>
  <span class="abs btn btn-blue">Read more <b>»</b></span>
</section>

<section class="mission">
  <div class="abs col" style="left:77px;width:480px">
    <h3><svg width="34" height="34" viewBox="0 0 34 34"><circle cx="17" cy="17" r="15" fill="none" stroke="#fff" stroke-width="3"/><circle cx="17" cy="17" r="9" fill="none" stroke="#fff" stroke-width="3"/><circle cx="17" cy="17" r="3" fill="#fff"/></svg>Our Mission</h3>
    <p>Lorem Ipsum is simply dummy text of the printing and type setting industry. Lorem Ipsum has been the industry's stand ard dummy text ever since the 1500s, when... <u>READ MORE</u></p>
  </div>
  <div class="abs divider"></div>
  <div class="abs col" style="left:604px">
    <h3><svg width="34" height="30" viewBox="0 0 34 30"><rect x="4" y="10" width="22" height="10" rx="3" transform="rotate(-25 15 15)" fill="#fff"/><rect x="24" y="4" width="6" height="12" rx="2" transform="rotate(-25 27 10)" fill="#fff"/></svg>Our Vision and Purpose</h3>
    <p>Lorem Ipsum is simply dummy text of the printing and type setting industry. Lorem Ipsum has been the industry's stand ard dummy text ever since the 1500s, when... <u>READ MORE</u></p>
  </div>
</section>

<section class="what">
  <h2 class="abs sec-title">WHAT <span class="accent">WE DO</span></h2>
  <p class="abs sec-sub">Lorem Ipsum is simply dummy text of the printing and typesetting industry. Lorem Ipsum has been the industry's standard dummy text ever since the 1500s.</p>
  <div class="abs card" style="left:77px;top:212px">
    <div class="photo" role="img" aria-label="Recruiters interviewing a candidate at a desk"></div>
    <h4>IT Recruiting</h4>
    <p>Lorem Ipsum is simply dummy text of the printing and typesetting industry. Lorem Ipsum has... <span class="more">Read more »</span></p>
  </div>
  <div class="abs card" style="left:438px;top:212px">
    <div class="photo" role="img" aria-label="Trainer presenting to a group at a whiteboard"></div>
    <h4>IT Training</h4>
    <p>Lorem Ipsum is simply dummy text of the printing and typesetting industry. Lorem Ipsum has... <span class="more">Read more »</span></p>
  </div>
  <div class="abs card" style="left:798px;top:212px">
    <div class="photo" role="img" aria-label="Laptop on a wooden desk" style="background:linear-gradient(135deg,#7a5a3c,#c9a37a 50%,#efe7dc)"></div>
    <h4>Hardware and software sales</h4>
    <p>Lorem Ipsum is simply dummy text of the printing and typesetting industry. Lorem Ipsum has... <span class="more">Read more »</span></p>
  </div>
</section>

<section class="why" role="img" aria-label="Blue tinted photo of an office team in the background">
  <h2 class="abs sec-title">WHY IT MATTERS</h2>
  <p class="abs sec-sub">Lorem Ipsum is simply dummy text of the printing and typesetting industry. Lorem Ipsum has been the industry's standard.</p>
  <div class="abs point" style="left:130px;width:430px">
    <div class="badge"><svg width="56" height="56" viewBox="0 0 56 56"><rect x="10" y="6" width="30" height="40" rx="2" fill="var(--orange)"/><circle cx="36" cy="38" r="10" fill="#fff" stroke="var(--orange)" stroke-width="4"/><line x1="43" y1="45" x2="50" y2="52" stroke="var(--orange)" stroke-width="5"/></svg></div>
    <div><h4>Quickly Fill Positions</h4><p>Lorem Ipsum is simply dummy text of the printing and typesetting industry. Lorem Ipsum has... <span class="more">Read more »</span></p></div>
  </div>
  <div class="abs point" style="left:622px;width:480px">
    <div class="badge"><svg width="56" height="56" viewBox="0 0 56 56"><path d="M6 46h12v-10h12v-10h12v-10h8" stroke="var(--orange)" stroke-width="5" fill="none"/><circle cx="24" cy="14" r="5" fill="var(--orange)"/><path d="M20 22l6 0 4 8-6 4z" fill="var(--orange)"/></svg></div>
    <div style="width:320px"><h4>Candidate Career Development</h4><p>Lorem Ipsum is simply dummy text of the printing and typesetting industry. Lorem Ipsum has... <span class="more">Read more »</span></p></div>
  </div>
</section>

<section class="diff">
  <h2 class="abs sec-title">WHAT MAKES US <span class="accent">DIFFERENT</span></h2>
  <p class="abs sec-sub">Lorem Ipsum is simply dummy text of the printing and typesetting industry. Lorem Ipsum has been the industry's standard dummy text ever since the 1500s.</p>
  <div class="abs tile" style="left:77px"><div class="photo" role="img" aria-label="Colleagues working together around a laptop"></div><h4>We Live What We Do</h4><p>Lorem Ipsum is simply dummy text of the printing and typeset industry... <span class="more">Read more »</span></p></div>
  <div class="abs tile" style="left:347px"><div class="photo" role="img" aria-label="Hands reviewing documents on a table"></div><h4 style="margin-top:14px">We Don't Compromise Quality</h4><p>Lorem Ipsum is simply dummy and types... <span class="more">Read more »</span></p></div>
  <div class="abs tile" style="left:619px"><div class="photo" role="img" aria-label="Presenter sharing charts with a small group"></div><h4>We Share Knowledge</h4><p>Lorem Ipsum is simply dummy text of the printing and typeset industry... <span class="more">Read more »</span></p></div>
  <div class="abs tile" style="left:889px"><div class="photo" role="img" aria-label="Business handshake"></div><h4>Staffing Guarantee</h4><p>Lorem Ipsum is simply dummy text of the printing and typeset industry... <span class="more">Read more »</span></p></div>
</section>

<section class="team" role="img" aria-label="Orange tinted photo of a business team in the background">
  <h2 class="abs sec-title">OUR TEAM</h2>
  <p class="abs sec-sub">Lorem Ipsum is simply dummy text of the printing and typesetting industry. Lorem Ipsum has been the industry's standard dummy text ever since the 1500s.</p>
  <div class="abs member" style="left:80px"><div class="photo" role="img" aria-label="Portrait of a team member"></div><h4>Lorem Ipsum is</h4><div class="row"><svg width="14" height="16" viewBox="0 0 14 16"><circle cx="7" cy="4" r="4" fill="#fff"/><path d="M0 16a7 7 0 0 1 14 0z" fill="#fff"/></svg><span>Lorem Ipsum is simply dummy.</span><svg width="20" height="14" viewBox="0 0 20 14"><rect width="20" height="14" rx="1" fill="#fff"/><path d="M0 1l10 7 10-7" stroke="var(--orange)" stroke-width="2" fill="none"/></svg></div></div>
  <div class="abs member" style="left:358px"><div class="photo" role="img" aria-label="Portrait of a team member"></div><h4>Lorem Ipsum is</h4><div class="row"><svg width="14" height="16" viewBox="0 0 14 16"><circle cx="7" cy="4" r="4" fill="#fff"/><path d="M0 16a7 7 0 0 1 14 0z" fill="#fff"/></svg><span>Lorem Ipsum is simply dummy.</span><svg width="20" height="14" viewBox="0 0 20 14"><rect width="20" height="14" rx="1" fill="#fff"/><path d="M0 1l10 7 10-7" stroke="var(--orange)" stroke-width="2" fill="none"/></svg></div></div>
  <div class="abs member" style="left:636px"><div class="photo" role="img" aria-label="Portrait of a team member"></div><h4>Lorem Ipsum is</h4><div class="row"><svg width="14" height="16" viewBox="0 0 14 16"><circle cx="7" cy="4" r="4" fill="#fff"/><path d="M0 16a7 7 0 0 1 14 0z" fill="#fff"/></svg><span>Lorem Ipsum is simply dummy.</span><svg width="20" height="14" viewBox="0 0 20 14"><rect width="20" height="14" rx="1" fill="#fff"/><path d="M0 1l10 7 10-7" stroke="var(--orange)" stroke-width="2" fill="none"/></svg></div></div>
  <div class="abs member" style="left:914px"><div class="photo" role="img" aria-label="Portrait of a team member"></div><h4>Lorem Ipsum is</h4><div class="row"><svg width="14" height="16" viewBox="0 0 14 16"><circle cx="7" cy="4" r="4" fill="#fff"/><path d="M0 16a7 7 0 0 1 14 0z" fill="#fff"/></svg><span>Lorem Ipsum is simply dummy.</span><svg width="20" height="14" viewBox="0 0 20 14"><rect width="20" height="14" rx="1" fill="#fff"/><path d="M0 1l10 7 10-7" stroke="var(--orange)" stroke-width="2" fill="none"/></svg></div></div>
  <span class="abs btn btn-blue">Meet with us <b>»</b></span>
</section>

<section class="contact">
  <h2 class="abs">CONTACT <span class="accent">US</span></h2>
  <h5 class="abs">TOVARIN</h5>
  <div class="abs info" style="left:77px;top:170px;width:260px"><svg width="14" height="20" viewBox="0 0 14 20"><path d="M7 0a7 7 0 0 1 7 7c0 5-7 13-7 13S0 12 0 7a7 7 0 0 1 7-7z" fill="var(--blue)"/><circle cx="7" cy="7" r="2.5" fill="#f0f0f0"/></svg><span>Lorem Ipsum is simply dummy text of the printing.</span></div>
  <div class="abs info" style="left:391px;top:168px"><svg width="16" height="16" viewBox="0 0 24 24"><path d="M6.6 10.8a15 15 0 0 0 6.6 6.6l2.2-2.2a1 1 0 0 1 1-.25 11.4 11.4 0 0 0 3.6.57 1 1 0 0 1 1 1V20a1 1 0 0 1-1 1A17 17 0 0 1 3 4a1 1 0 0 1 1-1h3.5a1 1 0 0 1 1 1c0 1.25.2 2.45.57 3.57a1 1 0 0 1-.25 1z" fill="var(--blue)"/></svg><span>(123) 456 - 7890</span></div>
  <div class="abs info" style="left:391px;top:200px"><svg width="16" height="14" viewBox="0 0 20 14"><rect width="20" height="14" rx="1" fill="var(--blue)"/><path d="M0 1l10 7 10-7" stroke="#f0f0f0" stroke-width="2" fill="none"/></svg><span>Lorem Ipsum simply</span></div>
  <div class="abs map" role="img" aria-label="Street map showing the office location"></div>
  <div class="abs field" style="top:140px">Name</div>
  <div class="abs field" style="top:201px">Email</div>
  <div class="abs field" style="top:264px">Subject</div>
  <div class="abs field msg" style="top:322px">Message</div>
  <span class="abs btn btn-blue">Submit</span>
</section>

<footer>
  <p class="abs">© TOVARIN BUSINESS SOLUTION LLC - 2016. All Rights Reserved.</p>
  <div class="abs social"><span class="dot"></span><span class="dot"></span><span class="dot"></span></div>
</footer>

</body>
</html>
```